Call Center In Need of Website Design

We are a call center that provides inbound and outbound calling & marketing services for eCommerce store. We would like to see a fun, creative, playful design that is simple.

Here are some sample design sites we like;
- https://www.velmoreline.com/
- https://pindrask.io/
- https://www.glimbertic.com/live-chat-software/
- https://www.zavrolin.com/

Here are some competitor sites;
- https://www.ostrevaglinks.com/
- https://www.helpkestrel.com/

I have attached website content for your use.

Target Market(s)

eCommerce

Coding

Coded - Design and coding required

Number of Pages Required

5+ page

Font styles to use
Sans Serif

Colors

Designer to choose colors to be used in the design.

Requirements
Must have
• Must have designs for the following 5 separate pages;
• 1. Home (landing)
• - This will be were the design style really needs to show.
• - Just needs to touch on key services
• - CTA
• 2. About Us
• - Basic page for about me paragraph
• 3. Services
• - List of services with icons
• - Click on service type to expand details or hover over service icon to view popup bubble with details about that service
• 4. Pricing
• - Option to bundle 1(one) digital service plan and 1(one) call center service plan
• - Bundling adds 10% monthly discount to over all price
• - Customer does NOT have to bundle
• - FAQ
• 5. Contact Us
• - Include a capture form (name, company name, email, phone, message)
• - Contact info
• - Business hours
• When customer purchases their desired plan, then they are taken to a page where they must schedule a call with an account rep.
Nice to have
• home page animations
Should not have
• All information on Home/Landing page.

```html
<!DOCTYPE html>
<html lang="en">
<head>
<meta charset="utf-8">
<title>Orbitra — Omnichannel Customer Care</title>
<link rel="stylesheet" href="https://fonts.googleapis.com/css2?family=Oswald:wght@500;700&family=Montserrat:wght@400;500;600&display=swap">
<style>
:root{
  --space:#38357f;
  --navy:#2e2b78;
  --teal:#63c3aa;
  --teal-dark:#56b39b;
  --teal-light:#84dcc3;
  --white:#ffffff;
  --ink:#222222;
  --grey:#8a8a8a;
  --line:#a9a9a9;
  --tip:#f1f1f1;
}
*{box-sizing:border-box;margin:0;padding:0}
html,body{width:1200px;height:2830px;overflow:hidden;background:var(--white)}
body{position:relative;font-family:"Montserrat",sans-serif;color:var(--ink)}
.abs{position:absolute}
.hero{left:0;top:0;width:1200px;height:430px;background:var(--space)}
.hero-art{left:790px;top:30px;width:390px;height:360px;background:linear-gradient(160deg,#4b4894,#2c2970);border-radius:40% 20% 10% 30%}
.rocket-art{left:62px;top:58px;width:24px;height:130px;background:linear-gradient(#63c3aa,#3e3b88);border-radius:12px 12px 4px 4px}
.brand{left:166px;top:30px;display:flex;align-items:center;gap:22px;color:var(--white);font-weight:500;font-size:34px;letter-spacing:6px}
.brand-dot{width:42px;height:42px;border-radius:50%;border:4px solid var(--teal)}
.nav{left:563px;top:44px;display:flex;gap:36px;list-style:none}
.nav li{color:var(--white);font-size:11px;font-weight:600;letter-spacing:.3px;text-transform:uppercase}
.nav li.active{border-bottom:2px solid var(--white);padding-bottom:6px}
.hero-title{left:160px;top:150px;color:var(--white);font-family:"Oswald",sans-serif;font-weight:700;font-size:58px;line-height:66px;letter-spacing:1px}
.hero-sub{left:162px;top:300px;color:var(--white);font-size:16px;letter-spacing:4.5px}
.clouds{left:0;top:350px;width:1200px;height:90px}
.about{left:0;top:430px;width:1200px;height:302px;background:var(--teal)}
.about-art{left:0;top:110px;width:150px;height:190px;background:linear-gradient(#7ad2ba,#4aa58d);border-radius:50% 50% 6px 6px}
.about-head{left:275px;top:86px;display:flex;align-items:center;gap:18px;color:var(--white);font-family:"Oswald",sans-serif;font-weight:700;font-size:28px}
.about-head::before{content:"";width:38px;height:8px;border-top:2px solid var(--white);border-bottom:2px solid var(--white)}
.about-text{left:325px;top:140px;width:570px;color:var(--white);font-size:10.5px;line-height:24px}
.about-text strong{font-weight:600}
.services-title{left:0;width:1200px;top:780px;text-align:center;font-family:"Oswald",sans-serif;font-weight:700;font-size:32px;color:var(--navy)}
.services-title::before{content:"";display:block;margin:0 auto 8px;width:36px;height:8px;border-top:2px solid var(--navy);border-bottom:2px solid var(--navy)}
.group-title{left:0;width:1200px;text-align:center;font-family:"Oswald",sans-serif;font-weight:700;font-size:17px;color:var(--ink)}
.group-title span{border-bottom:2px solid var(--ink);padding-bottom:2px}
.flow{left:0;top:0;width:1200px;height:1700px}
.svc{width:134px;height:86px;background:var(--space);border-radius:3px;color:var(--white);display:flex;flex-direction:column;align-items:center;justify-content:center;gap:6px;text-align:center;font-size:11px;font-weight:600;line-height:13px;padding:0 6px}
.svc svg{width:34px;height:30px}
.tip{left:249px;top:1664px;width:134px;height:170px;background:var(--tip);color:#555;font-size:11px;line-height:18px;text-align:center;padding:10px 10px}
.cta-title{left:0;width:1200px;top:1895px;text-align:center;font-family:"Oswald",sans-serif;font-weight:700;font-size:44px;line-height:54px;color:var(--navy);letter-spacing:1px}
.cta-btn{left:521px;top:2028px;width:158px;height:44px;border-radius:22px;background:var(--teal);color:var(--white);font-size:11px;font-weight:600;display:flex;align-items:center;justify-content:center;letter-spacing:.5px}
.cta-rocket{left:1010px;top:1925px;width:92px;height:265px;background:linear-gradient(#7ad2ba,#56b39b);border-radius:46px 46px 20px 20px;opacity:.9}
.contact{left:0;top:2180px;width:1200px;height:345px;background:var(--teal-dark)}
.contact-card{left:187px;top:62px;width:273px;height:262px;background:var(--teal-light);padding:28px 10px 0 24px;color:var(--white)}
.contact-card h3{font-size:15px;font-weight:600;margin-bottom:30px}
.contact-card ul{list-style:none;font-size:11px;line-height:17px}
.contact-card li{display:flex;gap:12px;margin-bottom:16px;white-space:nowrap}
.contact-card svg{flex:none;width:12px;height:14px;margin-top:2px}
.form-title{left:487px;top:55px;color:var(--white);font-size:28px;font-weight:500}
.field{width:254px;height:36px;background:var(--teal-light);color:var(--white);font-size:11px;padding:0 12px;display:flex;align-items:center}
.submit{left:487px;top:247px;width:106px;height:38px;border:2px solid var(--white);border-radius:6px;color:var(--white);font-size:11px;font-weight:600;display:flex;align-items:center;justify-content:center}
.copy{left:160px;top:2562px;font-size:11px;line-height:20px;color:#555}
.foot-nav{left:412px;top:2570px;display:flex;gap:32px;list-style:none;font-size:12px;color:#555}
.foot-nav .active{color:var(--teal)}
.social{left:919px;top:2565px;display:flex;gap:4px}
.social span{width:26px;height:26px;border-radius:2px;display:block}
</style>
</head>
<body>

<section class="abs hero" aria-label="Hero">
  <div class="abs rocket-art" role="img" aria-label="Illustration of a small rocket lifting off"></div>
  <div class="abs hero-art" role="img" aria-label="Illustration of a floating astronaut among stars"></div>
  <div class="abs brand"><span class="brand-dot"></span>ORBITRA</div>
  <ul class="abs nav">
    <li class="active">Home</li><li>About Us</li><li>Services</li><li>Pricing</li><li>Contact Us</li><li>Account</li>
  </ul>
  <h1 class="abs hero-title">Orbitra Is An<br>Omnichannel</h1>
  <p class="abs hero-sub">Provider For Customer Care</p>
</section>

<section class="abs about" aria-label="What we do">
  <div class="abs about-art" role="img" aria-label="Illustration of an astronaut planting a flag on the moon"></div>
  <h2 class="abs about-head">WHAT WE DO</h2>
  <p class="abs about-text">Orbitra is your personal customer service and product research team. We love eCommerce, but we love seeing business owners succeed even more! That is exactly why we have developed the processes and technology to take care of the most over looked areas in eCommerce - Customer Service and Retention. Let Orbitra handle your customers while you focus on growing your business.<br><strong>Let Orbitra handle your customers while you focus on growing your business.</strong></p>
</section>

<svg class="abs clouds" viewBox="0 0 1200 90" preserveAspectRatio="none" aria-hidden="true">
  <path fill="#63c3aa" d="M0 60 Q40 20 90 45 Q130 10 190 40 Q240 20 280 50 Q330 25 380 55 Q430 30 480 58 Q540 25 600 55 Q650 30 700 56 Q760 20 820 48 Q880 15 940 45 Q990 25 1040 50 Q1100 15 1160 42 Q1185 30 1200 40 V90 H0Z"/>
</svg>

<h2 class="abs services-title">Services</h2>
<h3 class="abs group-title" style="top:868px"><span>DIGITAL SERVICES</span></h3>
<h3 class="abs group-title" style="top:1183px"><span>CALL CENTER SERVICES</span></h3>

<svg class="abs flow" viewBox="0 0 1200 1700" aria-hidden="true">
  <defs><marker id="arrowhead" markerWidth="8" markerHeight="8" refX="4" refY="4" orient="auto"><path d="M0 0 L8 4 L0 8Z" fill="#a9a9a9"/></marker></defs>
  <g stroke="#a9a9a9" stroke-width="2" stroke-dasharray="2 4" fill="none">
    <path d="M600 905 V968" marker-end="url(#arrowhead)"/>
    <path d="M242 982 H954"/>
    <path d="M242 982 V1028" marker-end="url(#arrowhead)"/>
    <path d="M384 982 V1028" marker-end="url(#arrowhead)"/>
    <path d="M527 982 V1028" marker-end="url(#arrowhead)"/>
    <path d="M669 982 V1028" marker-end="url(#arrowhead)"/>
    <path d="M812 982 V1028" marker-end="url(#arrowhead)"/>
    <path d="M954 982 V1028" marker-end="url(#arrowhead)"/>

    <path d="M600 1222 V1286" marker-end="url(#arrowhead)"/>
    <path d="M242 1300 H954"/>
    <path d="M600 1300 V1515"/>
    <path d="M242 1300 V1343" marker-end="url(#arrowhead)"/>
    <path d="M384 1300 V1343" marker-end="url(#arrowhead)"/>
    <path d="M527 1300 V1343" marker-end="url(#arrowhead)"/>
    <path d="M669 1300 V1343" marker-end="url(#arrowhead)"/>
    <path d="M812 1300 V1343" marker-end="url(#arrowhead)"/>
    <path d="M954 1300 V1343" marker-end="url(#arrowhead)"/>

    <path d="M316 1515 H886"/>
    <path d="M316 1515 V1556" marker-end="url(#arrowhead)"/>
    <path d="M458 1515 V1556" marker-end="url(#arrowhead)"/>
    <path d="M601 1515 V1556" marker-end="url(#arrowhead)"/>
    <path d="M743 1515 V1556" marker-end="url(#arrowhead)"/>
    <path d="M886 1515 V1556" marker-end="url(#arrowhead)"/>
  </g>
</svg>

<!-- Digital services -->
<div class="abs svc" style="left:175px;top:1040px"><svg viewBox="0 0 34 30"><rect x="3" y="6" width="28" height="19" fill="none" stroke="#fff" stroke-width="2.5"/><path d="M3 6 L17 17 L31 6" fill="none" stroke="#fff" stroke-width="2.5"/></svg>Email Support</div>
<div class="abs svc" style="left:317px;top:1040px"><svg viewBox="0 0 34 30"><ellipse cx="17" cy="13" rx="14" ry="10" fill="#fff"/><path d="M8 20 L6 28 L15 22Z" fill="#fff"/></svg>Live Chat Support</div>
<div class="abs svc" style="left:460px;top:1040px"><svg viewBox="0 0 34 30"><path d="M17 2 L31 9 V22 L17 29 L3 22 V9Z" fill="#fff"/><path d="M3 9 L17 16 L31 9 M17 16 V29" stroke="#38357f" stroke-width="2" fill="none"/></svg>Product Research</div>
<div class="abs svc" style="left:602px;top:1040px"><svg viewBox="0 0 34 30"><rect x="8" y="2" width="18" height="26" fill="none" stroke="#fff" stroke-width="2.5"/><path d="M12 9 H22 M12 14 H22 M12 19 H22" stroke="#fff" stroke-width="2"/></svg>Product Listing</div>
<div class="abs svc" style="left:745px;top:1040px"><svg viewBox="0 0 34 30"><rect x="3" y="3" width="28" height="19" fill="none" stroke="#fff" stroke-width="2.5"/><path d="M13 22 V27 H21 V22 M9 15 L15 10 L19 13 L25 7" stroke="#fff" stroke-width="2" fill="none"/></svg>Price Monitoring</div>
<div class="abs svc" style="left:887px;top:1040px"><svg viewBox="0 0 34 30"><rect x="5" y="8" width="24" height="18" rx="2" fill="#fff"/><rect x="12" y="4" width="10" height="5" fill="#fff"/><circle cx="17" cy="17" r="5" fill="#38357f"/></svg>Product Photo &amp;<br>Video Editing</div>

<!-- Call center services -->
<div class="abs svc" style="left:175px;top:1355px"><svg viewBox="0 0 34 30"><path d="M6 18 V14 A11 11 0 0 1 28 14 V18" fill="none" stroke="#fff" stroke-width="2.5"/><rect x="3" y="16" width="6" height="9" rx="2" fill="#fff"/><rect x="25" y="16" width="6" height="9" rx="2" fill="#fff"/></svg>Answering service</div>
<div class="abs svc" style="left:317px;top:1355px"><svg viewBox="0 0 34 30"><circle cx="17" cy="14" r="11" fill="none" stroke="#fff" stroke-width="2.5"/><path d="M12 10 Q13 18 22 19" stroke="#fff" stroke-width="3" fill="none" stroke-linecap="round"/></svg>Welcome Calls</div>
<div class="abs svc" style="left:460px;top:1355px"><svg viewBox="0 0 34 30"><circle cx="14" cy="9" r="6" fill="#fff"/><path d="M3 27 Q4 16 14 16 Q22 16 24 22 V27Z" fill="#fff"/><circle cx="26" cy="22" r="6" fill="#fff"/><path d="M23 22 L25.5 24.5 L29 20" stroke="#38357f" stroke-width="2" fill="none"/></svg>Follow-Up Service</div>
<div class="abs svc" style="left:602px;top:1355px"><svg viewBox="0 0 34 30"><rect x="5" y="18" width="5" height="9" fill="#fff"/><rect x="13" y="13" width="5" height="14" fill="#fff"/><rect x="21" y="8" width="5" height="19" fill="#fff"/><path d="M4 12 L14 5 L22 7 L30 2" stroke="#fff" stroke-width="2" fill="none"/></svg>Customer Upselling</div>
<div class="abs svc" style="left:745px;top:1355px"><svg viewBox="0 0 34 30"><rect x="10" y="2" width="14" height="26" rx="2" fill="none" stroke="#fff" stroke-width="2.5"/><path d="M14 11 H20 M14 16 H20" stroke="#fff" stroke-width="2"/></svg>Over-The-Phone<br>Order Taking</div>
<div class="abs svc" style="left:887px;top:1355px"><svg viewBox="0 0 34 30"><path d="M8 4 L13 4 L15 10 L12 12 Q15 18 20 20 L22 17 L28 19 L28 24 Q16 27 8 4Z" fill="#fff"/><path d="M20 4 A8 8 0 0 1 28 12 M20 8 A4 4 0 0 1 24 12" stroke="#fff" stroke-width="2" fill="none"/></svg>Feedback/<br>Survey Calls</div>

<div class="abs svc" style="left:249px;top:1568px"><svg viewBox="0 0 34 30"><rect x="4" y="10" width="26" height="17" fill="none" stroke="#fff" stroke-width="2.5"/><path d="M17 3 V13 M13 9 L17 13 L21 9" stroke="#fff" stroke-width="2" fill="none"/></svg>Message Delivering<br>Service</div>
<div class="abs svc" style="left:392px;top:1568px"><svg viewBox="0 0 34 30"><rect x="8" y="3" width="18" height="25" fill="none" stroke="#fff" stroke-width="2.5"/><path d="M11 10 L13 12 L16 8 M18 10 H23 M11 18 L13 20 L16 16 M18 18 H23" stroke="#fff" stroke-width="1.8" fill="none"/></svg>ROI Diagnostics<br>&amp; Reporting</div>
<div class="abs svc" style="left:534px;top:1568px"><svg viewBox="0 0 34 30"><circle cx="17" cy="11" r="8" fill="#fff"/><path d="M5 28 Q6 19 17 19 Q28 19 29 28Z" fill="#fff"/></svg>Scalable Call<br>Center Pricing</div>
<div class="abs svc" style="left:677px;top:1568px"><svg viewBox="0 0 34 30"><path d="M6 26 L24 8 M10 4 L28 22" stroke="#fff" stroke-width="3" stroke-linecap="round"/><circle cx="25" cy="7" r="4" fill="none" stroke="#fff" stroke-width="2"/></svg>Customizable For<br>Any Industry</div>
<div class="abs svc" style="left:819px;top:1568px"><svg viewBox="0 0 34 30"><circle cx="16" cy="12" r="9" fill="#fff"/><path d="M10 19 L10 28 H20 L21 21Z" fill="#fff"/></svg>100% US-Based<br>Agents</div>

<p class="abs tip">Orbitra is your personal customer service and product research team. We love eCommerce, but we love seeing business owners succeed even more!</p>

<h2 class="abs cta-title">READY TO TAKE YOUR BUSINESS<br>TO THE NEXT LEVEL</h2>
<div class="abs cta-btn">GET STARTED</div>

<section class="abs contact" aria-label="Contact">
  <div class="abs contact-card">
    <h3>Contact Details</h3>
    <ul>
      <li><svg viewBox="0 0 12 14"><path d="M2 1 H5 L6 4 L4 5 Q5 8 8 9 L9 7 L12 8 V11 Q5 13 2 1Z" fill="#fff"/></svg>Phone: (800) 555-0142</li>
      <li><svg viewBox="0 0 12 14"><rect x="0" y="3" width="12" height="8" fill="#fff"/></svg>hello@orbitra.example</li>
      <li><svg viewBox="0 0 12 14"><path d="M6 14 Q0 7 0 5 A6 6 0 0 1 12 5 Q12 7 6 14Z" fill="#fff"/></svg><span>Orbitra, Inc.<br>418 Larkspur Ave. Brisvale, CA 95012</span></li>
    </ul>
  </div>
  <h2 class="abs form-title">Request For Call Back</h2>
  <div class="abs field" style="left:487px;top:135px">Name</div>
  <div class="abs field" style="left:757px;top:135px">Email</div>
  <div class="abs field" style="left:487px;top:188px">Ph Num</div>
  <div class="abs field" style="left:757px;top:188px">Enquiry About</div>
  <div class="abs submit">Submit Now</div>
</section>
<div class="abs cta-rocket" role="img" aria-label="Illustration of a rocket launching from a cloud of smoke"></div>

<footer>
  <p class="abs copy">Copyright © 2018<br>All rights reserved</p>
  <ul class="abs foot-nav">
    <li class="active">Home</li><li>About Us</li><li>Service</li><li>Pricing</li><li>Contact Us</li><li>Account</li>
  </ul>
  <div class="abs social" aria-label="Social links">
    <span style="background:#2aa3e0"></span><span style="background:#3b5a9a"></span><span style="background:#3f729b"></span><span style="background:#dc4a38"></span>
  </div>
</footer>

</body>
</html>
```